Social Media App Needs PPT Template

We need a PowerPoint template for a new social media company based in the DC area called "Bold Ledger." We provide an interactive digital platform for executives to share actionable advice. We would like to see designs that use our orange logo color as an accent, but are mainly grey, white, and black. The final design should communicate clean, chic, modern, and professional.

Target Market(s)

Executives

Industry/Entity Type

Information Technology

Font styles to use
Sans Serif

Colors
f78f20
fbe7d2
ffffff
000000
e8e8e8
757575

Requirements
Must have
• My project must have title page and many options for the body of the ppt (graphs, tables, etc). It also needs to be easy to modify. I must have someone who is experienced in creating powerpoint templates.
Nice to have
• It would be nice to have a very modern and clean design that includes the logo on every page, but still leaves a lot of room for the content of the slide
Should not have
• My design project should not look to busy.

```html
<!DOCTYPE html>
<html lang="en">
<head>
<meta charset="UTF-8">
<title>Bold Ledger – About Our Company</title>
<link href="https://fonts.googleapis.com/css2?family=Lato:wght@300;400&display=swap" rel="stylesheet">
<style>
  :root {
    --backdrop: #555555;
    --slide-bg: #f4f4f4;
    --orange: #f0921f;
    --orange-deep: #e8821a;
    --navy: #232e3e;
    --grey: #6d6d6e;
    --ink: #231f20;
    --white: #ffffff;
    --label: #e6e6e6;
    --footer-text: #c9ccd2;
  }
  * { margin: 0; padding: 0; box-sizing: border-box; }
  html, body { width: 1200px; height: 960px; overflow: hidden; }
  body {
    background: var(--backdrop);
    font-family: 'Lato', sans-serif;
    position: relative;
  }
  .page-label {
    position: absolute; top: 74px; left: 0; width: 1200px;
    text-align: center; color: var(--label);
    font-weight: 300; font-size: 28px;
  }
  .slide {
    position: absolute; left: 111px; top: 135px;
    width: 970px; height: 728px;
    background: radial-gradient(ellipse at 50% 40%, #ffffff 0%, var(--slide-bg) 60%, #ececec 100%);
    overflow: hidden;
  }
  .slide-frame { position: absolute; inset: 0; }
  .slide-title {
    position: absolute; left: 30px; top: 62px;
    color: var(--white); font-weight: 300; font-size: 37px; line-height: 1;
  }
  .brand {
    position: absolute; left: 790px; top: 70px;
    display: flex; align-items: center; gap: 9px;
  }
  .brand-dot { width: 18px; height: 18px; border-radius: 50%; background: var(--orange); }
  .brand-name { color: var(--white); font-size: 21px; font-weight: 400; letter-spacing: 0.5px; }

  .stat-card {
    position: absolute; width: 330px; height: 176px;
    color: var(--white);
  }
  .stat-card--orange { background: var(--orange); }
  .stat-card--grey { background: var(--grey); }
  .stat-card--navy { background: var(--navy); }
  .stat-card--ink { background: var(--ink); }
  .stat-value {
    position: absolute; left: 78px; top: 27px;
    font-size: 35px; font-weight: 400; line-height: 1;
  }
  .stat-text {
    position: absolute; left: 77px; top: 71px; width: 240px;
    font-size: 16.5px; line-height: 20px; font-weight: 400;
  }
  .stat-icon {
    position: absolute; width: 106px; height: 106px; border-radius: 50%;
    border: 3px solid var(--white);
    display: flex; align-items: center; justify-content: center;
    box-shadow: 0 0 0 1px rgba(0,0,0,0.04);
  }
  .stat-icon svg { width: 60px; height: 60px; }

  .footer-url {
    position: absolute; left: 26px; top: 695px;
    color: var(--footer-text); font-size: 13px; font-weight: 300;
  }
</style>
</head>
<body>
  <div class="page-label">Page 11</div>

  <section class="slide">
    <svg class="slide-frame" width="970" height="728" viewBox="0 0 970 728">
      <polygon points="749,33 970,33 970,42 740,42" fill="var(--orange)"/>
      <polygon points="0,46 737,46 661,122 0,122" fill="var(--orange-deep)"/>
      <polygon points="560,46 737,46 705,78 520,78" fill="var(--orange)" opacity="0.6"/>
      <polygon points="0,106 676,106 661,122 0,122" fill="var(--orange)" opacity="0.5"/>
      <polygon points="743,46 970,46 970,122 663,122" fill="var(--navy)"/>
      <polygon points="0,126 653,126 645,135 0,135" fill="var(--navy)"/>
      <polygon points="0,689 277,689 249,718 0,718" fill="var(--navy)"/>
      <polygon points="283,689 970,689 970,718 255,718" fill="var(--orange-deep)"/>
    </svg>

    <h1 class="slide-title">About Our Company</h1>
    <div class="brand"><span class="brand-dot"></span><span class="brand-name">Bold Ledger</span></div>

    <article class="stat-card stat-card--orange" style="left:106px; top:196px;">
      <div class="stat-value">915,456,459</div>
      <p class="stat-text">Lorem ipsum dolor sit amet, consectetuer adipiscing elit, s ed diam nonu mmy nibh euis mod tincidunt</p>
    </article>
    <div class="stat-icon" style="left:53px; top:235px; background:var(--orange);">
      <svg viewBox="0 0 60 60" fill="none" stroke="#fff" stroke-width="3" stroke-linejoin="round" stroke-linecap="round">
        <rect x="4" y="22" width="8" height="14"/>
        <polygon points="12,22 38,12 38,46 12,36"/>
        <rect x="38" y="10" width="5" height="38"/>
        <polyline points="18,38 21,47 28,45 26,40"/>
        <line x1="48" y1="22" x2="54" y2="20"/><line x1="48" y1="29" x2="55" y2="29"/><line x1="48" y1="36" x2="54" y2="38"/>
      </svg>
    </div>

    <article class="stat-card stat-card--grey" style="left:571px; top:196px;">
      <div class="stat-value" style="left:73px;">111,458,564</div>
      <p class="stat-text" style="left:75px;">Lorem ipsum dolor sit amet, consectetuer adipiscing elit, s ed diam nonu mmy nibh euis mod tincidunt</p>
    </article>
    <div class="stat-icon" style="left:521px; top:235px; background:var(--grey);">
      <svg viewBox="0 0 60 60" fill="none" stroke="#fff" stroke-width="3" stroke-linejoin="round" stroke-linecap="round">
        <rect x="22" y="6" width="16" height="8" rx="2"/>
        <path d="M24 14 C12 24 6 36 10 46 C12 52 18 54 30 54 C42 54 48 52 50 46 C54 36 48 24 36 14 Z"/>
        <path d="M35 30 C33 27 25 27 25 32 C25 37 35 35 35 40 C35 45 27 45 25 42"/>
        <line x1="30" y1="24" x2="30" y2="48"/>
      </svg>
    </div>

    <article class="stat-card stat-card--navy" style="left:106px; top:442px;">
      <div class="stat-value" style="top:30px;">100%</div>
      <p class="stat-text" style="top:73px;">Lorem ipsum dolor sit amet, consectetuer adipiscing elit, s ed diam nonu mmy nibh euis mod tincidunt</p>
    </article>
    <div class="stat-icon" style="left:53px; top:481px; background:var(--navy);">
      <svg viewBox="0 0 60 60" fill="none" stroke="#fff" stroke-width="3" stroke-linecap="round">
        <circle cx="30" cy="30" r="20"/>
        <path d="M36 23 C34 19 24 19 24 25 C24 31 36 29 36 35 C36 41 26 41 24 37"/>
        <line x1="30" y1="15" x2="30" y2="45"/>
      </svg>
    </div>

    <article class="stat-card stat-card--ink" style="left:571px; top:442px;">
      <div class="stat-value" style="left:73px; top:28px;">100%</div>
      <p class="stat-text" style="left:75px; top:71px;">Lorem ipsum dolor sit amet, consectetuer adipiscing elit, s ed diam nonu mmy nibh euis mod tincidunt</p>
    </article>
    <div class="stat-icon" style="left:521px; top:479px; background:var(--ink);">
      <svg viewBox="0 0 60 60" fill="none" stroke="#fff" stroke-width="3" stroke-linejoin="round">
        <rect x="8" y="38" width="9" height="12"/>
        <rect x="20" y="28" width="9" height="22"/>
        <rect x="32" y="18" width="9" height="32"/>
        <rect x="44" y="8" width="9" height="42"/>
      </svg>
    </div>

    <div class="footer-url">www.boldledger.com &nbsp;|&nbsp; Page 9</div>
  </section>
</body>
</html>
```